Harborlane Products Flyer

Harborlane Lending Group, Inc.
Licensed Mortgage Company
Serving the DMV since 1997
"You open the Harborlane, we'll carry the load"
We specialize in...
FHA Loans
* Credit Scores as low as 500
* 203K Renovation Loans
Conventional Loans
* As little as 1% Down
* Bank Statement for Self-Employed
Investor Loans
* DSCR, & Fix & Flip
* Commercial & New Construction
Other Programs
* HELOCS & Reverse Mortgages
Call today for a free consultation
(800) 914-6027
www.harborlanehomeloans.com
NMLS #731860

```html
<!DOCTYPE html>
<html lang="en">
<head>
<meta charset="utf-8">
<title>Harborlane Products Flyer</title>
<link href="https://fonts.googleapis.com/css2?family=Cinzel:wght@400;600;700&family=Oswald:wght@400;500&family=Montserrat+Alternates:wght@400&display=swap" rel="stylesheet">
<style>
  :root {
    --navy: #021820;
    --teal: #0d4a5c;
    --gold: #f8c45a;
    --gold-deep: #c9922e;
    --cream: #fde9c4;
    --ink: #0c1a22;
    --paper: #ffffff;
    --backdrop: #e9e6e1;
    --photo-light: #eeeae6;
    --photo-warm: #b98a6c;
  }
  * { box-sizing: border-box; margin: 0; padding: 0; }
  html, body { width: 991px; height: 1200px; overflow: hidden; background: var(--backdrop); }
  .flyer {
    position: absolute; left: 70px; top: 62px; width: 846px; height: 1075px;
    background: var(--paper); color: var(--ink); overflow: hidden;
  }
  .brand { position: absolute; left: 14px; top: 52px; width: 250px; text-align: center; font-family: "Cinzel", serif; color: var(--navy); }
  .brand-name { font-size: 26px; font-weight: 700; line-height: 1.05; }
  .brand-name small { display: block; font-size: 15px; font-weight: 700; margin-top: 4px; }
  .brand-tagline { font-size: 9px; font-weight: 600; margin-top: 12px; letter-spacing: .2px; }
  .brand-est { font-size: 10px; font-weight: 700; letter-spacing: 2px; margin-top: 6px; }
  .contact { position: absolute; left: 440px; top: 52px; }
  .contact-icon { position: absolute; left: 0; top: 4px; width: 50px; height: 52px; }
  .contact-lead { position: absolute; left: 62px; top: 0; white-space: nowrap; font-family: "Cinzel", serif; font-size: 13.5px; letter-spacing: .4px; }
  .contact-phone { position: absolute; left: 60px; top: 16px; white-space: nowrap; font-family: "Cinzel", serif; font-size: 40px; font-weight: 400; }
  .serving { position: absolute; left: 450px; top: 125px; white-space: nowrap; font-family: "Cinzel", serif; font-size: 23px; font-weight: 600; letter-spacing: .5px; }
  .hero-photo {
    position: absolute; left: 0; top: 191px; width: 851px; height: 327px;
    background: linear-gradient(100deg, var(--photo-light) 0%, #d9c8bb 30%, var(--photo-warm) 45%, #d8c6b8 60%, var(--photo-light) 80%);
  }
  .panel-tab { position: absolute; top: 170px; width: 0; height: 0; border-bottom: 20px solid var(--teal); }
  .panel-tab.left { left: 421px; border-left: 14px solid transparent; }
  .panel-tab.right { left: 818px; border-right: 14px solid transparent; }
  .panel {
    position: absolute; left: 435px; top: 170px; width: 383px; height: 373px;
    background: var(--navy); color: var(--gold); text-align: right; padding-right: 24px;
    font-family: "Oswald", sans-serif;
  }
  .panel-kicker { position: absolute; right: 24px; top: 22px; font-size: 25px; font-weight: 500; }
  .panel-line1 { position: absolute; right: 24px; top: 76px; font-size: 58px; line-height: 1; white-space: nowrap; }
  .panel-name { position: absolute; right: 24px; top: 150px; font-family: "Cinzel", serif; font-weight: 700; font-size: 46px; line-height: 1; }
  .panel-line2 { position: absolute; right: 24px; top: 230px; font-size: 42px; line-height: 1; white-space: nowrap; }
  .panel-nmls { position: absolute; right: 24px; top: 318px; font-size: 26px; font-weight: 500; }
  .specialize { position: absolute; left: 38px; top: 568px; font-family: "Cinzel", serif; font-size: 43px; font-weight: 600; letter-spacing: 1px; }
  .product { position: absolute; width: 381px; height: 107px; border: 1.5px solid var(--navy); }
  .product-icon { position: absolute; left: 13px; top: 23px; width: 60px; height: 60px; border-radius: 50%; background: var(--cream); }
  .product-icon svg { width: 60px; height: 60px; }
  .product-title { position: absolute; left: 91px; top: 18px; font-family: "Cinzel", serif; font-size: 18px; font-weight: 600; letter-spacing: .5px; white-space: nowrap; }
  .product-list { position: absolute; left: 91px; top: 48px; list-style: none; font-family: "Montserrat Alternates", sans-serif; font-size: 13.5px; line-height: 22.5px; white-space: nowrap; }
  .p-fha { left: 37px; top: 643px; }
  .p-conv { left: 429px; top: 643px; }
  .p-inv { left: 37px; top: 778px; }
  .p-other { left: 429px; top: 778px; }
  .p-other .product-title { top: 28px; }
  .p-other .product-list { top: 58px; }
  .about { position: absolute; left: 38px; top: 913px; width: 400px; font-family: "Montserrat Alternates", sans-serif; font-size: 13.5px; line-height: 25px; }
  .badges { position: absolute; left: 557px; top: 931px; }
  .badge { position: absolute; }
  .badge-a { left: 0; top: 0; width: 38px; height: 38px; background: #1d4fa0; }
  .badge-b { left: 63px; top: 4px; width: 44px; height: 32px; background: #222; }
  .badge-c { left: 133px; top: 8px; width: 114px; height: 24px; background: #b8232f; }
  .footer { position: absolute; left: 0; top: 1019px; width: 851px; height: 56px; background: var(--navy); color: var(--gold); display: flex; align-items: center; justify-content: center; font-family: "Cinzel", serif; font-size: 20px; letter-spacing: 3px; }
</style>
</head>
<body>
<main class="flyer">
  <header class="brand">
    <div class="brand-name">Harborlane<small>Lending Group, Inc.</small></div>
    <div class="brand-tagline">You open the Harborlane, we'll carry the load</div>
    <div class="brand-est">EST. 1997</div>
  </header>

  <div class="contact">
    <svg class="contact-icon" viewBox="0 0 50 52" fill="none" stroke="var(--navy)" stroke-width="2.6" stroke-linecap="round" stroke-linejoin="round">
      <path d="M10 8 l7 -3 l6 12 l-5 4 c2 6 7 11 13 14 l4 -5 l12 6 l-3 7 c-2 4 -8 5 -14 2 c-11 -5 -20 -15 -24 -26 c-2 -5 0 -9 4 -11z"/>
      <path d="M28 10 c6 1 11 6 12 12"/>
      <path d="M30 2 c9 1 16 8 17 17"/>
    </svg>
    <div class="contact-lead">Call today for a free consultation</div>
    <div class="contact-phone">(800) 914-6027</div>
  </div>
  <div class="serving">Serving the DMV since 1997</div>

  <div class="hero-photo" role="img" aria-label="Smiling family of four seated together on a white bed"></div>

  <span class="panel-tab left"></span>
  <span class="panel-tab right"></span>
  <section class="panel">
    <div class="panel-kicker">Licensed Mortgage Company</div>
    <div class="panel-line1">You Open The</div>
    <div class="panel-name">Harborlane</div>
    <div class="panel-line2">We’ll Carry The Load</div>
    <div class="panel-nmls">NMLS #731860</div>
  </section>

  <h2 class="specialize">We specialize in...</h2>

  <article class="product p-fha">
    <div class="product-icon">
      <svg viewBox="0 0 60 60" fill="none" stroke="var(--ink)" stroke-width="1.6" stroke-linecap="round" stroke-linejoin="round">
        <circle cx="36" cy="20" r="7"/><path d="M36 15 v10 M33.5 18 c0 -2 5 -2 5 0 s-5 1 -5 3 s5 2 5 0"/>
        <path d="M14 40 c5 -4 10 -5 15 -3 h7 c2 0 2 3 0 3 h-8 M28 40 l10 -4 c3 -1 5 2 2 4 l-11 6 h-15"/>
      </svg>
    </div>
    <h3 class="product-title">FHA Loans</h3>
    <ul class="product-list"><li>* Credit Scores as low as 500</li><li>* 203K Renovation Loans</li></ul>
  </article>

  <article class="product p-conv">
    <div class="product-icon">
      <svg viewBox="0 0 60 60" fill="none" stroke="var(--ink)" stroke-width="1.6" stroke-linecap="round" stroke-linejoin="round">
        <path d="M12 22 c6 -4 12 -4 16 -1 h8 c2 0 2 3 0 3 h-7 M29 24 l10 -2 h6 M45 18 v10 h4 v-10z"/>
        <circle cx="24" cy="36" r="6"/><path d="M24 32 v8 M22 34.5 c0 -1.5 4 -1.5 4 0 s-4 1 -4 2.5 s4 1.5 4 0"/>
        <path d="M15 30 c-2 4 -1 9 3 11"/>
      </svg>
    </div>
    <h3 class="product-title">Conventional Loans</h3>
    <ul class="product-list"><li>* As little as 1% Down</li><li>* Bank Statement for Self-Employed</li></ul>
  </article>

  <article class="product p-inv">
    <div class="product-icon">
      <svg viewBox="0 0 60 60" fill="none" stroke="var(--ink)" stroke-width="1.6" stroke-linecap="round" stroke-linejoin="round">
        <path d="M14 28 l16 -13 l16 13 M18 25 v17 h24 v-17"/>
        <circle cx="30" cy="28" r="3"/><rect x="33" y="33" width="5" height="9"/>
        <rect x="13" y="34" width="12" height="10" fill="var(--navy)"/>
        <path d="M16 42 l6 -6" stroke="var(--cream)"/>
      </svg>
    </div>
    <h3 class="product-title">Investor Loans</h3>
    <ul class="product-list"><li>* DSCR, &amp; Fix &amp; Flip</li><li>* Commercial &amp; New Construction</li></ul>
  </article>

  <article class="product p-other">
    <div class="product-icon">
      <svg viewBox="0 0 60 60" fill="none" stroke="var(--ink)" stroke-width="1.6" stroke-linecap="round" stroke-linejoin="round">
        <rect x="16" y="17" width="28" height="5" rx="2"/><rect x="16" y="24" width="28" height="5" rx="2"/>
        <circle cx="30" cy="22" r="6" fill="var(--cream)"/><path d="M30 18.5 v7"/>
        <path d="M13 40 c5 -4 10 -5 15 -3 h7 c2 0 2 3 0 3 h-8 M28 40 l10 -4 c3 -1 5 2 2 4 l-11 6 h-15"/>
      </svg>
    </div>
    <h3 class="product-title">Other Programs</h3>
    <ul class="product-list"><li>* HELOCS &amp; Reverse Mortgages</li></ul>
  </article>

  <p class="about">We have served the MD, DC &amp; VA area by providing an array of mortgage loan products tailored to our clients unique needs and desires.</p>

  <div class="badges" aria-hidden="true">
    <span class="badge badge-a"></span>
    <span class="badge badge-b"></span>
    <span class="badge badge-c"></span>
  </div>

  <footer class="footer">www.harborlanehomeloans.com</footer>
</main>
</body>
</html>
```